Buch-/eBook-Cover für Traumatherapeutin
Zielgruppe
Ich bin Traumatherapeutin und schreibe ein Buch zum Thema Trauma bearbeiten.
Meine Zielgruppe sucht Heilung, Genesung, Selbstliebe etc.
Aufgabenstellung
Buchcover
Bitte erstell mir ein modernes positives inspirierendes Buchcover mit dem
Titel: 'Morgenlicht NEU entdecken“
Untertitel: „Spüre den Mut der ganz in dir wohnt“
Dr. Mira Kessow
Ich hätte gerne ein modernes Buch, das entweder einen Bezug zum Thema Trauma hat oder aber einfach stylische Schriftzüge. Bin aber auch offen für andere Vorschläge.
Dunkelblau, weiß und türkis oder auch rosa mag ich ganz gerne. Wobei Dunkelblau, weiß und türkis meine Favoriten sind und mit rosa höchstens kleinere Akzente gesetzt werden sollten.
Das Buchcover soll modern sein und direkt ansprechen. Gerne eine originelle Lösung, oder etwas Besonderes, etwas das Tiefe ausdrückt, oder man mehrmals hinsehen muss um etwas zu erkennen oder etwas das mehr Interpretationsspielraum lässt.
Gerne auch viel weiß, zumindest heller und nicht zu dunkel. Stylish, aber nicht überfrachtet.
Schreib mich gerne an, wenn du Fragen hast.
Ich habe mal zwei Beispiel von Typolösungen angehängt, die ich ganz cool fände.
Ich freue mich auf deine Ideen :-)
Ganz liebe Grüße
Mira

```html
<!DOCTYPE html>
<html lang="de">
<head>
<meta charset="utf-8">
<title>Morgenlicht NEU entdecken – Buchcover</title>
<link rel="stylesheet" href="https://fonts.googleapis.com/css2?family=Playfair+Display:wght@400&family=Lato:wght@400&display=swap">
<style>
  :root {
    --page-bg: #efefef;
    --cover-blue: #435a88;
    --glow-turquoise: #6ad8e6;
    --glow-mid: #5aa5c0;
    --accent-turquoise: #6dd9e6;
    --text-white: #ffffff;
  }
  * { margin: 0; padding: 0; box-sizing: border-box; }
  html, body {
    width: 1200px;
    height: 1199px;
    overflow: hidden;
    background: var(--page-bg);
  }
  .cover {
    position: absolute;
    left: 313px;
    top: 170px;
    width: 573px;
    height: 859px;
    background:
      radial-gradient(circle 420px at 100% 0%,
        var(--glow-turquoise) 0%,
        rgba(90, 165, 192, 0.7) 45%,
        rgba(67, 90, 136, 0) 100%),
      var(--cover-blue);
    overflow: hidden;
  }
  .cover-illustration {
    position: absolute;
    left: 107px;
    top: 416px;
    width: 403px;
    height: 310px;
    background: radial-gradient(ellipse 60% 70% at 80% 35%,
      rgba(109, 217, 230, 0.75) 0%,
      rgba(90, 165, 192, 0.35) 50%,
      rgba(67, 90, 136, 0) 100%);
  }
  .title {
    position: absolute;
    left: 52px;
    top: 130px;
    font-family: "Playfair Display", Georgia, serif;
    font-weight: 400;
    font-size: 68px;
    line-height: 75px;
    color: var(--text-white);
  }
  .title span { display: block; }
  .title .title-accent { color: var(--accent-turquoise); }
  .subtitle {
    position: absolute;
    left: 52px;
    top: 412px;
    font-family: "Lato", Arial, sans-serif;
    font-size: 21px;
    line-height: 29.5px;
    color: var(--text-white);
  }
  .subtitle span { display: block; }
  .author {
    position: absolute;
    left: 0;
    right: 0;
    top: 778px;
    text-align: center;
    font-family: "Lato", Arial, sans-serif;
    font-size: 25px;
    letter-spacing: 0.13em;
    color: var(--text-white);
    text-transform: uppercase;
  }
</style>
</head>
<body>
  <main class="cover">
    <div class="cover-illustration" role="img" aria-label="Illustration: Lichtschein, der aus einer geöffneten Tür auf den Boden fällt"></div>

    <h1 class="title">
      <span>Morgenlicht</span>
      <span class="title-accent">NEU</span>
      <span>entdecken</span>
    </h1>

    <p class="subtitle">
      <span>Spüre den Mut</span>
      <span>der ganz in dir wohnt</span>
    </p>

    <p class="author">Dr. Mira Kessow</p>
  </main>
</body>
</html>
```